Summit Bodyform Gym Website

We need a website design for our gym.

Summit is the UAE's first calisthenics and parkour gym. The theme under which the gym revolves is that one does not require any machinery to workout as our bodies could be themselves the machinery. The gym is designed to be the more of a social hub rather than an "in-and-out" gym, where people come train, have fun, hang out and socialize for a few hours rather than just train for 60 minutes then leave. The gym is designed to be a big open space with lots of natural sunlight, natural wood and plants all over the place to create a natural and refreshing setting. We also use recycled material throughout the gym and recycle our waste as being green is part of our philosophy. We currently also have some of the world's top and most recognized calisthenics athletes working with us.

We would like our website to reflect all that as well as provide a simple, interactive and fun way for visitors to be able to get class and gym information, check out gym media and contact us for bookings.

Target Market(s)

Ages 15-35

Industry/Entity Type

Fitness

Coding

Coded - Design and coding required

Number of Pages Required

4 page

Font styles to use
Decorative

Colors
0792cd

Requirements
Must have
• Class descriptions
• Gym description
• Class schedules
• Trainer profiles
• Gym philosophy
• Contact Details
Nice to have
• A link to contact us directly for a free first trial class

```html
<!DOCTYPE html>
<html lang="en">
<head>
<meta charset="utf-8">
<title>Summit Bodyform Gym</title>
<link href="https://fonts.googleapis.com/css2?family=Roboto:wght@300;400;500;700&display=swap" rel="stylesheet">
<style>
:root{
  --brand:#0792cd;
  --brand-bright:#1aa6d6;
  --ink:#2b2b2b;
  --muted:#555;
  --soft:#f1f1f1;
  --line:#d9d9d9;
  --dark:#333;
  --star:#f0a030;
  --sat:#9fd8f2;
  --sun:#6cc2e6;
  --cal-red:#e0474c;
}
*{box-sizing:border-box;margin:0;padding:0}
html,body{width:1200px;height:2601px;overflow:hidden}
body{font-family:'Roboto',sans-serif;color:var(--ink);background:#fff;position:relative}
.section{position:absolute;left:0;width:1200px}
.wrap{position:absolute;left:75px;width:1052px}

/* top bar */
.topbar{top:0;height:45px;background:var(--soft)}
.login{position:absolute;right:75px;top:14px;font-size:12px;color:#555;display:flex;align-items:center;gap:6px}
.login svg{width:13px;height:13px}

/* header */
.header{top:45px;height:87px;background:#fff}
.brand{position:absolute;left:75px;top:0;height:87px;display:flex;align-items:center}
.brand-name{font-size:22px;font-weight:500;color:var(--ink);line-height:1}
.nav{position:absolute;right:73px;top:47px;display:flex;gap:31px;font-size:14px;color:#333}
.nav .active{color:var(--brand)}

/* hero */
.hero{top:132px;height:515px;background:linear-gradient(160deg,#6d7b84 0%,#a9b4ba 30%,#8b4a3c 62%,#6c3025 100%)}
.hero-tagline{position:absolute;right:76px;top:166px;text-align:right}
.hero-tagline span{display:inline-block;background:rgba(30,30,30,.55);color:#fff;font-size:30px;font-weight:500;padding:2px 10px;margin-bottom:6px;line-height:1.25}
.hero-cta{position:absolute;right:76px;top:280px;background:var(--brand-bright);color:#fff;font-size:16px;font-weight:500;padding:9px 18px}
.dots{position:absolute;right:82px;top:364px;display:flex;gap:6px}
.dots i{width:9px;height:9px;border-radius:50%;background:#fff;display:block}
.dots i:first-child{background:#222}

/* welcome */
.welcome{top:647px;height:432px}
.welcome-text{position:absolute;left:0;top:61px;width:578px}
.welcome h2{font-size:26px;font-weight:400;padding-bottom:12px;border-bottom:1px dashed #ccc}
.welcome p{font-size:12.5px;line-height:24px;color:var(--muted);margin-top:18px;text-align:justify}
.read-more{display:flex;align-items:center;gap:6px;font-size:12.5px;font-weight:500;margin-top:14px;letter-spacing:.3px}
.coach{position:absolute;left:627px;top:60px;width:425px}
.coach h3{font-size:25px;font-weight:500;color:var(--brand)}
.video{margin-top:14px;height:281px;border:4px solid #fff;box-shadow:0 0 6px rgba(0,0,0,.3);position:relative;background:linear-gradient(180deg,#ececec,#c9c9c9)}
.video .play{position:absolute;left:50%;top:42%;transform:translate(-50%,-50%)}
.controls{position:absolute;left:0;right:0;bottom:0;height:36px;background:#3a3a3a;display:flex;align-items:center;padding:0 12px;gap:12px}
.track{flex:1;height:3px;background:#777;position:relative;margin-left:8px}
.track::before{content:"";position:absolute;left:0;top:0;height:3px;width:30%;background:var(--cal-red)}

/* services */
.services{top:1079px;height:357px;background:linear-gradient(100deg,#6b6b6b 0%,#3d3d3d 45%,#202020 100%)}
.services h2{position:absolute;left:75px;top:47px;color:#fff;font-size:29px;font-weight:300}
.services h2 b{font-weight:500}
.service{position:absolute;top:134px;width:331px;height:165px;border:1px solid rgba(255,255,255,.6);color:#fff;padding:56px 20px 0}
.service svg{position:absolute;left:20px;top:-30px}
.service h4{font-size:15px;font-weight:500}
.service p{font-size:12.5px;line-height:20px;margin-top:8px;color:#ddd;text-align:justify}

/* gallery */
.gallery{top:1436px;height:518px}
.gallery h2{position:absolute;left:83px;top:52px;font-size:27px;font-weight:400}
.gallery h2 b{font-weight:500}
.tile{position:absolute}
.feature{background:var(--brand-bright);opacity:.95;color:#fff;text-align:center;padding-top:88px}
.feature h4{font-size:19px;font-weight:400;letter-spacing:.5px}
.feature p{font-size:13px;line-height:19px;margin:10px 22px 0}
.feature .btns{display:flex;justify-content:center;gap:14px;margin-top:14px}
.feature .btns span{width:30px;height:30px;border:2px solid #fff;display:flex;align-items:center;justify-content:center}

/* trainers + schedule */
.people{top:1954px;height:456px;background:var(--soft)}
.people h2{font-size:27px;font-weight:400}
.people h2 b{font-weight:500}
.trainers{position:absolute;left:75px;top:50px;width:497px}
.trainer{display:flex;gap:16px;margin-top:24px}
.trainer+.trainer{border-top:1px solid #ddd;padding-top:24px}
.avatar{width:76px;height:76px;flex:none;margin-left:6px;background:linear-gradient(160deg,#d9c2a8,#b88f72)}
.trainer h4{font-size:15px;font-weight:500;color:var(--brand)}
.trainer p{font-size:12.5px;line-height:20px;color:var(--muted);margin-top:8px}
.stars{display:flex;gap:3px;margin-top:6px}
.people .read-more{margin-top:18px;margin-left:6px}
.schedule{position:absolute;left:614px;top:50px;width:513px}
.cal-head{display:flex;justify-content:space-between;align-items:center;margin-top:14px;font-size:15px}
.cal-nav{display:flex;gap:4px}
.cal-nav i{width:16px;height:16px;border-radius:50%;background:#333;display:block}
.cal-nav i+i{background:#ccc}
table{width:100%;border-collapse:collapse;margin-top:4px;background:#fff;border:1px solid #999}
th{background:var(--cal-red);color:#fff;font-size:7px;font-weight:500;height:10px;border-left:1px solid #fff}
th.wk{background:#444}
td{border:1px solid #aaa;height:57px;font-size:10px;text-align:right;vertical-align:top;padding:3px 5px}
td.sat{background:var(--sat)}
td.sun{background:var(--sun)}
td.off{background:#ddd}
td.wk{width:47px;text-align:center;vertical-align:middle;padding-top:14px}

/* newsletter */
.newsletter{top:2410px;height:122px;background:#fff}
.newsletter h2{position:absolute;left:161px;top:45px;font-size:32px;font-weight:400;letter-spacing:.5px}
.email{position:absolute;left:345px;top:44px;width:496px;height:44px;border:1px solid var(--line);display:flex;align-items:center;padding-left:14px;gap:12px;font-size:12.5px;color:#888}
.subscribe{position:absolute;left:858px;top:44px;width:181px;height:44px;background:var(--brand-bright);color:#fff;font-size:15px;font-weight:500;letter-spacing:1px;display:flex;align-items:center;justify-content:center}

/* footer */
.footer{top:2532px;height:69px;background:var(--dark);color:#ddd}
.footer small{position:absolute;left:73px;top:27px;font-size:12px}
.social{position:absolute;right:78px;top:19px;display:flex;gap:12px}
.social i{width:28px;height:28px;border:2px solid #ddd;border-radius:50%;display:block}
</style>
</head>
<body>

<div class="section topbar">
  <div class="login">
    <svg viewBox="0 0 16 16"><circle cx="8" cy="5" r="3.5" fill="#0792cd"/><path d="M1 16c0-4 3-6 7-6s7 2 7 6z" fill="#0792cd"/></svg>
    Log In/Join ⌄
  </div>
</div>

<header class="section header">
  <div class="brand"><span class="brand-name">Summit Bodyform Gym</span></div>
  <nav class="nav">
    <span class="active">Home</span><span>Class descriptions</span><span>Gym description</span><span>Class schedules</span><span>Trainer profiles</span><span>Gym philosophy</span><span>Contact</span>
  </nav>
</header>

<section class="section hero" role="img" aria-label="Photo of the gym floor with blue mats, wooden walls and climbing boards">
  <div class="hero-tagline">
    <span>Your body is the machine</span><br>
    <span>train, play and hang out at Summit</span>
  </div>
  <div class="hero-cta">FREE FIRST TRIAL CLASS</div>
  <div class="dots"><i></i><i></i><i></i><i></i></div>
</section>

<section class="section welcome">
  <div class="wrap">
    <div class="welcome-text">
      <h2>Welcome to Summit</h2>
      <p>Lorem Ipsum is simply dummy text of the printing and typesetting industry. Lorem Ipsum has been the industry's standard dummy text ever since the 1500s, when an unknown printer took a galley of type and scrambled it to make a type specimen book. It has survived not only five centuries, but also the leap into electronic typesetting, remaining essentially unchanged. It was popularised in the 1960s with the release of transfer sheets containing Lorem Ipsum passages, and more recently with desktop publishing software and page layout tools. It was popularised in the 1960s with the release of transfer sheets containing Lorem Ipsum passages, and more recently with desktop publishing software and page layout tools. It was popularised in the 1960s with the release of transfer sheets containing Lorem Ipsum passages, and more.</p>
      <div class="read-more">READ MORE <svg width="13" height="13" viewBox="0 0 14 14"><circle cx="7" cy="7" r="6" fill="none" stroke="#2b2b2b" stroke-width="1.6"/><path d="M6 4l3 3-3 3" fill="none" stroke="#2b2b2b" stroke-width="1.6"/></svg></div>
    </div>
    <div class="coach">
      <h3>Trainers Coaching</h3>
      <div class="video" role="img" aria-label="Video still of a trainer holding a stopwatch">
        <svg class="play" width="66" height="66" viewBox="0 0 66 66"><circle cx="33" cy="33" r="30" fill="rgba(0,0,0,.15)" stroke="#fff" stroke-width="3"/><path d="M26 20l20 13-20 13z" fill="#fff"/></svg>
        <div class="controls">
          <svg width="10" height="12" viewBox="0 0 10 12"><path d="M0 0l10 6-10 6z" fill="#fff"/></svg>
          <svg width="10" height="12" viewBox="0 0 10 12"><rect width="3" height="12" fill="#fff"/><rect x="6" width="3" height="12" fill="#fff"/></svg>
          <div class="track"></div>
        </div>
      </div>
    </div>
  </div>
</section>

<section class="section services" role="img" aria-label="Dark blurred photo of gym equipment">
  <h2>Our <b>Services</b></h2>
  <div class="service" style="left:75px">
    <svg width="92" height="64" viewBox="0 0 92 64"><g fill="#1aa6d6"><circle cx="46" cy="10" r="7"/><rect x="36" y="19" width="20" height="26" rx="4"/><rect x="38" y="44" width="6" height="18"/><rect x="48" y="44" width="6" height="18"/><rect x="6" y="24" width="80" height="4"/><rect x="4" y="12" width="8" height="28" rx="2"/><rect x="80" y="12" width="8" height="28" rx="2"/></g></svg>
    <h4>NEQUE PORRO</h4>
    <p>Lorem Ipsum passages, and more recently with desktop publishing software and page layout tools.</p>
  </div>
  <div class="service" style="left:434px">
    <svg width="92" height="64" viewBox="0 0 92 64"><g fill="#1aa6d6"><circle cx="66" cy="40" r="16"/><circle cx="30" cy="10" r="6"/><path d="M26 18l8 2-6 24h28v6H20z"/><rect x="6" y="56" width="50" height="5"/><rect x="40" y="6" width="4" height="40" transform="rotate(30 42 26)"/></g></svg>
    <h4>DOLOREM IPSUM</h4>
    <p>Lorem Ipsum passages, and more recently with desktop publishing software and page layout tools.</p>
  </div>
  <div class="service" style="left:794px">
    <svg width="92" height="64" viewBox="0 0 92 64"><g fill="#1aa6d6"><rect x="2" y="28" width="88" height="6"/><rect x="8" y="14" width="9" height="34" rx="2"/><rect x="20" y="8" width="10" height="46" rx="2"/><rect x="62" y="8" width="10" height="46" rx="2"/><rect x="75" y="14" width="9" height="34" rx="2"/></g></svg>
    <h4>NEQUE PORRO</h4>
    <p>Lorem Ipsum passages, and more recently with desktop publishing software and page layout tools.</p>
  </div>
</section>

<section class="section gallery">
  <h2>Our <b>Gallery</b></h2>
  <div class="tile" style="left:83px;top:106px;width:243px;height:350px;background:linear-gradient(180deg,#a97a4e 0%,#5e7a3a 35%,#8e3c30 70%,#7a2f25 100%)" role="img" aria-label="Gym wall with plants above a dumbbell rack"></div>
  <div class="tile" style="left:349px;top:106px;width:241px;height:163px;background:linear-gradient(160deg,#2b3038,#586470 60%,#3a4048)" role="img" aria-label="Climbing frame with equipment"></div>
  <div class="tile" style="left:349px;top:291px;width:241px;height:165px;background:linear-gradient(180deg,#d6d6d6,#8a8a8a 60%,#5a5a5a)" role="img" aria-label="Black calisthenics rig in an open hall"></div>
  <div class="tile feature" style="left:612px;top:106px;width:243px;height:350px">
    <h4>NEQUE PORRO</h4>
    <p>Lorem ipsum dolor sit amet, consectetur adipiscing elit, sed do eiusmod tempor.</p>
    <div class="btns">
      <span><svg width="14" height="14" viewBox="0 0 14 14"><circle cx="6" cy="6" r="4.5" fill="none" stroke="#fff" stroke-width="1.8"/><path d="M9 9l4 4" stroke="#fff" stroke-width="1.8"/></svg></span>
      <span><svg width="14" height="14" viewBox="0 0 14 14"><path d="M6 8l2-2M5 6L3 8a2 2 0 003 3l2-2M9 8l2-2a2 2 0 00-3-3L6 5" fill="none" stroke="#fff" stroke-width="1.6"/></svg></span>
    </div>
  </div>
  <div class="tile" style="left:876px;top:106px;width:242px;height:163px;background:linear-gradient(170deg,#4f7f95,#2c3e4a 60%,#20262c)" role="img" aria-label="Gymnastic ring hanging from a blue frame"></div>
  <div class="tile" style="left:876px;top:291px;width:242px;height:165px;background:linear-gradient(180deg,#7b6a58,#9d4a38 55%,#1aa6d6 85%)" role="img" aria-label="Training floor with blue mats"></div>
</section>

<section class="section people">
  <div class="trainers">
    <h2><b>Trainer</b> Profiles</h2>
    <div class="trainer">
      <div class="avatar" role="img" aria-label="Trainer portrait"></div>
      <div>
        <h4>Nora Vale</h4>
        <p>Lorem Ipsum passages, and more recently with desktop publishing software and page layout tools. Lorem Ipsum passages, and more recently with desktop software.</p>
        <div class="stars"><svg width="86" height="14" viewBox="0 0 86 14"><g fill="#f0a030"><path id="s" d="M7 0l2 5h5l-4 3 2 5-5-3-5 3 2-5-4-3h5z"/><use href="#s" x="18"/><use href="#s" x="36"/><use href="#s" x="54"/></g><use href="#s" x="72" fill="#ccc"/></svg></div>
      </div>
    </div>
    <div class="trainer">
      <div class="avatar" role="img" aria-label="Trainer portrait"></div>
      <div>
        <h4>Tariq Stone</h4>
        <p>Lorem Ipsum passages, and more recently with desktop publishing software and page layout tools. Lorem Ipsum passages, and more recently with desktop software.</p>
        <div class="stars"><svg width="86" height="14" viewBox="0 0 86 14"><g fill="#f0a030"><use href="#s"/><use href="#s" x="18"/><use href="#s" x="36"/><use href="#s" x="54"/></g><use href="#s" x="72" fill="#ccc"/></svg></div>
      </div>
    </div>
    <div class="read-more">READ MORE</div>
  </div>

  <div class="schedule">
    <h2><b>Class</b> Schedules</h2>
    <div class="cal-head"><span>December 2015</span><div class="cal-nav"><i></i><i></i></div></div>
    <table>
      <tr><th>MONDAY</th><th>TUESDAY</th><th>WEDNESDAY</th><th>THURSDAY</th><th>FRIDAY</th><th>SATURDAY</th><th>SUNDAY</th><th class="wk">WEEK</th></tr>
      <tr><td class="off"></td><td>1</td><td>2</td><td>3</td><td>4</td><td class="sat">5</td><td class="sun">6</td><td class="wk">49</td></tr>
      <tr><td>7</td><td>8</td><td>9</td><td>10</td><td>11</td><td class="sat">12</td><td class="sun">13</td><td class="wk">50</td></tr>
      <tr><td>14</td><td>15</td><td>16</td><td>17</td><td>18</td><td class="sat">19</td><td class="sun">20</td><td class="wk">51</td></tr>
      <tr><td>21</td><td>22</td><td>23</td><td>24</td><td>25</td><td class="sat">26</td><td class="sun">27</td><td class="wk">52</td></tr>
      <tr><td>28</td><td>29</td><td>30</td><td>31</td><td class="off"></td><td class="off"></td><td class="off"></td><td class="wk">53</td></tr>
    </table>
  </div>
</section>

<section class="section newsletter">
  <h2>Newsletter</h2>
  <div class="email"><svg width="16" height="12" viewBox="0 0 16 12"><rect x="1" y="1" width="14" height="10" fill="none" stroke="#555" stroke-width="1.4"/><path d="M1 1l7 6 7-6" fill="none" stroke="#555" stroke-width="1.4"/></svg>Enter your Email</div>
  <div class="subscribe">SUBSCRIBE</div>
</section>

<footer class="section footer">
  <small>Copyright © 2015 Yoursitename. All rights reserved.</small>
  <div class="social"><i></i><i></i><i></i><i></i></div>
</footer>

</body>
</html>
```